Web Design

We are Carvendo’s new and used car supermarket, we need a clean and nice look web design.

What included on homepage:
1. Logo
2. Slideshow (additional)
3. Menu - Home, About us, New cars, Used cars, Contact us
4. Advance Search
5. Customer Reviews
6. Social links - facebook, twitter , youtube
7. Banner Ads
8. Recent News
9. Newsletter

We just need psd files, home and contact us.

Industry/Entity Type

Used Car

Number of Pages Required

2 page

Requirements
Must have
• Webpage are well designed and in accordance with the color of the logo that is displayed in the file attachment.

```html
<!DOCTYPE html>
<html lang="en">
<head>
<meta charset="utf-8">
<title>Carvendo – Contact us</title>
<link rel="stylesheet" href="https://fonts.googleapis.com/css2?family=Arimo:wght@400;700&display=swap">
<style>
:root{
  --blue:#1565b0;
  --blue-dark:#0c4f95;
  --blue-deep:#0a3f7a;
  --blue-field:#3a7ab8;
  --red:#f50f1a;
  --yellow:#ffd200;
  --orange:#f5a623;
  --page:#e9e9e9;
  --white:#ffffff;
  --ink:#1b4f8a;
  --line:#d6d6d6;
  --ad:#c4c4c4;
  --map:#dcd8cc;
}
*{box-sizing:border-box;margin:0;padding:0}
html,body{width:836px;height:1200px;overflow:hidden}
body{position:relative;background:var(--page);font-family:"Arimo",Arial,sans-serif;color:var(--ink)}
.abs{position:absolute}

/* header */
.site-header{left:0;top:0;width:836px;height:86px;background:var(--page)}
.brand{left:22px;top:14px;display:flex;align-items:center;gap:10px}
.brand-mark{width:14px;height:14px;background:var(--red)}
.brand-name{font-size:42px;font-weight:700;color:var(--blue);letter-spacing:1px;line-height:1}
.tagline{left:305px;top:30px;font-size:24px;font-weight:700;color:var(--blue)}
.contact-info{right:14px;top:6px;text-align:right;color:var(--blue);font-weight:700}
.contact-info .phone{font-size:14px}
.contact-info .email{font-size:11px;margin-top:2px}
.social-top{right:12px;top:38px;display:flex;gap:4px}
.social-top span{width:28px;height:28px;display:block}

/* nav */
.main-nav{left:0;top:86px;width:836px;height:33px;background:var(--blue);display:flex;padding-left:22px}
.main-nav a{color:var(--white);text-decoration:none;font-size:14px;line-height:33px;padding:0 13px}
.main-nav a.active{border-top:3px solid var(--red);line-height:27px;background:var(--blue-dark)}

/* search */
.search-band{left:0;top:119px;width:836px;height:99px;background:var(--red)}
.search-field{top:20px}
.search-field label{display:block;color:var(--yellow);font-size:14px;margin-bottom:2px}
.select{width:134px;height:28px;background:var(--white);border:1px solid #999;position:relative}
.select::after{content:"";position:absolute;right:8px;top:11px;border:4px solid transparent;border-top:5px solid #000}
.price-track{left:541px;top:159px;width:125px;height:8px;border-radius:4px;background:var(--blue-dark)}
.price-knob{width:14px;height:14px;border-radius:50%;background:var(--orange);top:155px}
.price-label{left:537px;top:140px;color:var(--yellow);font-size:14px}
.price-range{left:537px;top:172px;color:var(--yellow);font-size:13px}
.btn-search{left:726px;top:154px;width:96px;height:30px;background:var(--blue);color:var(--white);font-size:12px;text-align:center;line-height:30px;border:1px solid #0d4d8a}
.advanced{left:726px;top:186px;color:var(--yellow);font-size:11px}

/* map */
.map{left:0;top:218px;width:836px;height:214px;background:linear-gradient(135deg,#e4e1d6,var(--map) 50%,#cfd6c6)}
.map-label{left:0;top:313px;width:836px;text-align:center;font-size:30px;color:#3a3330}
.map-tab{left:0;top:218px;width:200px;height:40px;background:var(--white)}

/* breadcrumb */
.crumb-bar{left:0;top:432px;width:836px;height:46px;background:#dedede}
.crumb{left:16px;top:440px;width:804px;height:26px;background:#ebebeb;font-size:11px;color:#8a8a8a;padding:7px 8px}

/* contact panel */
.contact-panel{left:16px;top:489px;width:594px;height:487px;background:var(--white)}
.contact-panel h1{position:absolute;left:6px;top:10px;font-size:24px;color:var(--ink)}
.contact-panel .intro{position:absolute;left:6px;top:40px;width:580px;font-size:11.5px;line-height:20px;color:var(--ink)}
.field{position:absolute}
.field label{display:block;font-size:11.5px;color:var(--ink);margin-bottom:5px}
.input{width:197px;height:24px;border:1px solid var(--line);background:var(--white)}
.textarea{width:401px;height:96px;border:1px solid var(--line)}
.pill{border-radius:10px;background:var(--blue);color:var(--white);font-size:10px;text-align:center}
.btn-send{left:5px;top:342px;width:46px;height:20px;line-height:20px}

/* sidebar */
.banner-ad{left:624px;top:489px;width:198px;height:233px;background:var(--ad);color:var(--white);font-size:24px;text-align:center;padding-top:90px;line-height:30px}
.newsletter{left:624px;top:733px;width:198px;height:243px;background:var(--white);border:2px solid var(--blue);padding:30px 16px 0 20px}
.newsletter h2{font-size:11.5px;color:var(--ink);margin-bottom:12px}
.newsletter p{font-size:10px;line-height:12px;color:var(--ink);margin-bottom:11px}
.nl-input{width:164px;height:20px;background:var(--blue-field);color:var(--white);font-size:9.5px;padding:4px 3px;margin-left:-4px;margin-bottom:8px;border:1px solid #2a5f95}
.btn-subscribe{width:46px;height:19px;line-height:19px;margin-left:-4px;margin-top:2px}

/* footer */
.site-footer{left:0;top:985px;width:836px;height:215px;background:var(--blue)}
.f-col{top:1009px;color:var(--white)}
.f-col h3{font-size:11px;font-weight:700;margin-bottom:14px}
.f-about p{font-size:8.5px;line-height:15px;width:125px}
.f-news li{list-style:none;font-size:9px;line-height:15.5px}
.f-news li::before{content:"";display:inline-block;width:6px;height:6px;border-radius:50%;background:var(--white);margin-right:3px}
.f-in{position:absolute;background:var(--blue-field);border:1px solid #6a9fd0;color:var(--white);font-size:8.5px;padding:3px 4px}
.f-send{position:absolute;left:395px;top:1132px;width:42px;height:16px;line-height:16px;font-size:8.5px;background:var(--blue-dark)}
.follow span{position:absolute;width:30px;height:30px;border:2px solid var(--white);border-radius:50%}
.f-bottom{left:185px;top:1160px;width:465px;height:40px;background:var(--blue-deep);color:var(--white);font-size:7px;padding:18px 26px;display:flex;justify-content:space-between}
</style>
</head>
<body>

<header class="site-header abs">
  <div class="brand abs"><span class="brand-mark"></span><span class="brand-name">CARVENDO</span></div>
  <div class="tagline abs">Best Car Supermarket</div>
  <div class="contact-info abs">
    <div class="phone">Call : (555) 0142 0187</div>
    <div class="email">hello@carvendo.example</div>
  </div>
  <div class="social-top abs">
    <span style="background:#f39c12"></span>
    <span style="background:#d9442f"></span>
    <span style="background:#3b5b98"></span>
    <span style="background:#1ea3e0"></span>
  </div>
</header>

<nav class="main-nav abs">
  <a href="#">Home</a><a href="#">About us</a><a href="#">New cars</a><a href="#">Used cars</a><a class="active" href="#">Contact us</a>
</nav>

<section class="search-band abs" aria-label="Advanced search"></section>
<div class="search-field abs" style="left:22px;top:136px"><label>Manufacture</label><div class="select"></div></div>
<div class="search-field abs" style="left:193px;top:136px"><label>Model</label><div class="select"></div></div>
<div class="search-field abs" style="left:364px;top:136px"><label>Colour</label><div class="select"></div></div>
<div class="price-label abs">Price</div>
<div class="price-track abs"></div>
<div class="price-knob abs" style="left:537px"></div>
<div class="price-knob abs" style="left:597px"></div>
<div class="price-range abs">$0 - $1000</div>
<div class="btn-search abs">Search</div>
<div class="advanced abs">Advanced Search</div>

<div class="map abs" role="img" aria-label="Street map showing the dealership location"></div>
<div class="map-tab abs"></div>
<div class="map-label abs">Your Map Address</div>

<div class="crumb-bar abs"></div>
<div class="crumb abs">Home \ Contact us</div>

<main class="contact-panel abs">
  <h1>Contact us</h1>
  <p class="intro">If you have any further queries, requests or suggestions, we will be pleased to assist you. Please select the subject of your enquiry to ensure your question is forwarded to the correct department. You can contact us online and we will get back to you as soon as possible.</p>
  <div class="field" style="left:5px;top:125px"><label>First Name</label><div class="input"></div></div>
  <div class="field" style="left:208px;top:125px"><label>Last Name</label><div class="input"></div></div>
  <div class="field" style="left:5px;top:175px"><label>Choose Category</label><div class="input"></div></div>
  <div class="field" style="left:208px;top:175px"><label>Subject</label><div class="input"></div></div>
  <div class="field" style="left:5px;top:224px"><label>Massage</label><div class="textarea"></div></div>
  <div class="pill btn-send abs">Send</div>
</main>

<aside class="banner-ad abs">250 x 295<br>banner Ad</aside>
<aside class="newsletter abs">
  <h2>Newsletter</h2>
  <p>If you want to daily news and updates ?<br>Fill the form and send us for daily updates.</p>
  <div class="nl-input">First Name</div>
  <div class="nl-input">Last Name</div>
  <div class="nl-input">Email</div>
  <div class="pill btn-subscribe">Subscribe</div>
</aside>

<footer class="site-footer abs"></footer>
<div class="f-col f-about abs" style="left:52px">
  <h3>Short About us</h3>
  <p>Carvendo's is a top supermarket all our the world.We are Carvendo's new and used car supermarket .More d about you company text here write.</p>
</div>
<div class="f-col f-news abs" style="left:235px">
  <h3>News &amp; Updates</h3>
  <ul><li>News update 1</li><li>News update 2</li><li>News update 3</li><li>News update 4</li><li>News update 5</li></ul>
</div>
<div class="f-col abs" style="left:395px"><h3>Email us</h3></div>
<div class="f-in" style="left:395px;top:1033px;width:87px;height:17px">First Name</div>
<div class="f-in" style="left:486px;top:1033px;width:86px;height:17px">Last Name</div>
<div class="f-in" style="left:395px;top:1055px;width:177px;height:17px">Email</div>
<div class="f-in" style="left:395px;top:1077px;width:177px;height:48px">Message</div>
<div class="pill f-send">Send</div>
<div class="f-col abs" style="left:635px"><h3>Follow us</h3></div>
<div class="follow">
  <span style="left:635px;top:1040px"></span><span style="left:673px;top:1040px"></span><span style="left:711px;top:1040px"></span>
  <span style="left:635px;top:1078px"></span><span style="left:673px;top:1078px"></span><span style="left:711px;top:1078px"></span>
</div>
<div class="f-bottom abs">
  <span>Copyright © 2014 - By Carvendo . All Rights Reserved.</span>
  <span>Home / About us / New car / Used car / Contact us</span>
</div>

</body>
</html>
```